Name of business TRV Harbor Asset Partners, LP.
business focuses on hotel investments and real estate deals, on the bottom of the card I need my partner company listed as "Strategic Partner of Velmora Lodging Group" www.velmoralodginggroup-example.com and the logo that is attached for them on the bottom also

I am the Principal of the business

Industry/Entity Type

Real Estate

Contact Information for Business Card

Devin Marsh
287 Quarry Lane
Millbrook, KS 66021
C- 555-302-1846
D- 555-719-2063
F- 555-864-3371

```html
<!DOCTYPE html>
<html lang="en">
<head>
<meta charset="utf-8">
<title>TRV Harbor Asset Partners – Business Card</title>
<link href="https://fonts.googleapis.com/css2?family=Quicksand:wght@500;700&display=swap" rel="stylesheet">
<style>
  :root {
    --slate: #3e5068;
    --paper: #ffffff;
    --ink-navy: #1c2477;
    --backdrop: #dfe2e6;
    --brand-blue: #2a9fd8;
  }
  html, body {
    margin: 0;
    width: 1200px;
    height: 1000px;
    overflow: hidden;
    background: var(--backdrop);
  }
  .card {
    position: absolute;
    left: 75px;
    top: 200px;
    width: 1050px;
    height: 600px;
    background: var(--paper);
    box-shadow: 0 6px 20px rgba(0,0,0,0.18);
    font-family: "Quicksand", sans-serif;
    overflow: hidden;
  }
  .card-shapes { position: absolute; inset: 0; }
  .card-shapes .slate { fill: var(--slate); }
  .card-shapes .paper { fill: var(--paper); }

  .holder-name {
    position: absolute;
    left: 130px;
    top: 183px;
    margin: 0;
    font-size: 40px;
    font-weight: 700;
    color: var(--ink-navy);
    letter-spacing: 0.5px;
  }
  .contact-line {
    position: absolute;
    left: 360px;
    width: 260px;
    margin: 0;
    font-size: 27px;
    font-weight: 500;
    color: var(--ink-navy);
    text-align: center;
    line-height: 46px;
  }
  .contact-line.cell { top: 282px; }
  .contact-line.direct { top: 347px; }
  .contact-line.fax { top: 412px; }

  .company-block {
    position: absolute;
    left: 40px;
    top: 488px;
    color: var(--paper);
  }
  .company-name { margin: 0; font-size: 29px; font-weight: 500; }
  .company-address { margin: 4px 0 0; font-size: 25px; font-weight: 500; }

  .partner-brand {
    position: absolute;
    left: 745px;
    top: 292px;
    display: flex;
    align-items: center;
    gap: 10px;
    white-space: nowrap;
  }
  .partner-brand .brand-dot {
    width: 16px; height: 16px;
    border-radius: 50%;
    background: var(--brand-blue);
  }
  .partner-brand .brand-name {
    font-size: 22px;
    font-weight: 700;
    color: var(--brand-blue);
  }

  .partner-info {
    position: absolute;
    left: 722px;
    top: 414px;
    width: 320px;
    text-align: center;
    color: var(--paper);
    white-space: nowrap;
  }
  .partner-tagline { margin: 0; font-size: 15px; font-weight: 500; }
  .partner-url { margin: 14px 0 0; font-size: 15.5px; font-weight: 500; }
</style>
</head>
<body>
  <div class="card">
    <svg class="card-shapes" viewBox="0 0 1050 600" width="1050" height="600" aria-hidden="true">
      <polygon class="slate" points="0,0 640,0 690,600 0,600"/>
      <polygon class="slate" points="700,380 1050,380 1050,600 718,600"/>
      <polygon class="paper" points="0,172 657,172 663,244 0,244"/>
      <polygon class="paper" points="300,282 640,282 640,328 345,328"/>
      <polygon class="paper" points="300,347 640,347 640,393 345,393"/>
      <polygon class="paper" points="300,412 640,412 640,458 345,458"/>
    </svg>

    <h1 class="holder-name">Devin Marsh</h1>
    <p class="contact-line cell">C : 555-302-1846</p>
    <p class="contact-line direct">D : 555-719-2063</p>
    <p class="contact-line fax">F : 555-864-3371</p>

    <div class="company-block">
      <p class="company-name">TRV Harbor Asset Partners, LP</p>
      <p class="company-address">287 Quarry Lane Millbrook, KS 66021</p>
    </div>

    <div class="partner-brand">
      <span class="brand-dot"></span>
      <span class="brand-name">Velmora Lodging Group</span>
    </div>

    <div class="partner-info">
      <p class="partner-tagline">“Strategic Partner of Velmora Lodging Group”</p>
      <p class="partner-url">www.velmoralodginggroup-example.com</p>
    </div>
  </div>
</body>
</html>
```